Web design for a honey company

We are a honey retailing company currently looking for creative design for 3 pages of our existing e-commerce website which can be found here www.alpha.tolvenmarsk.co.nz. The designs need to be responsive i.e. presented in both desktop and mobile versions. We want to use the existing page color pallet, however any fonts can be used. Please use the texts and graphic content in the attachment files provided. For more detailed instructions please. The page does not require coding, the output files should be provided as layered and editable PSD.<br/><br/>Task 2: design 2 home page banners. Images, texts and the concept provided in the "layout structure" file. <br/><br/>The web designs should be presented in both desktop and mobile versions. We are looking for professional designer submissions only!

Target Market(s)

Hi-end consumers
Health conscious consumers

Number of Pages Required

3 page

Requirements
Must have
• 50% of images supplied along + any suggested stock images.
• Supplied texts integrated in the designs.
• Please only use the product images we have provided!
Should not have
• Clipart vector bees, vector honey slots or combs.
• No images of honey in glass jars!
• Do not use images of the traditional honey wooden spoons!
• Do not use images of any other but Manuka flower!

```html
<!DOCTYPE html>
<html lang="en">
<head>
<meta charset="utf-8">
<title>Tolvenmarsk — Manuka Honey</title>
<link href="https://fonts.googleapis.com/css2?family=Bangers&family=Lato:wght@400;700&family=Montserrat:wght@500;600&family=Playfair+Display:wght@700&family=Oswald:wght@500&display=swap" rel="stylesheet">
<style>
:root{
  --gold:#d4a52a;
  --gold-dark:#c8980e;
  --gold-light:#f1d272;
  --cream:#fdf9ea;
  --ink:#111;
  --text:#555;
  --muted:#777;
  --footer:#232326;
  --footer-base:#1a1a1c;
  --white:#fff;
}
*{margin:0;padding:0;box-sizing:border-box}
html,body{width:1200px;height:3292px;overflow:hidden;background:var(--white)}
body{position:relative;font-family:"Lato",sans-serif;color:var(--text)}
.abs{position:absolute}
.brand{display:flex;align-items:center;gap:10px;font-family:"Montserrat",sans-serif;font-weight:600;font-size:17px;letter-spacing:2px;color:var(--gold)}
.brand .dot{width:22px;height:22px;border-radius:50%;background:var(--gold)}
.nav{left:335px;top:62px;display:flex;gap:29px;font-family:"Lato",sans-serif;font-size:13px;letter-spacing:.5px;color:#888}
.nav .active{color:var(--ink);font-weight:700}
.cart{left:782px;top:46px;width:48px;height:48px;border-radius:50%;background:var(--gold);display:flex;align-items:center;justify-content:center;box-shadow:0 2px 6px rgba(0,0,0,.15)}
.hero-bg{left:804px;top:0;width:396px;height:625px;background:linear-gradient(180deg,var(--gold-light),var(--gold))}
.call{left:932px;top:44px;display:flex;gap:12px;align-items:center}
.call small{display:block;font-family:"Montserrat",sans-serif;font-size:11px;color:#222}
.call strong{font-family:"Oswald",sans-serif;font-weight:500;font-size:21px;color:var(--ink)}
.hero-circle{left:596px;top:146px;width:416px;height:416px;border-radius:50%;background:var(--white);box-shadow:0 0 24px rgba(210,170,60,.15)}
.jar-photo{background:linear-gradient(160deg,#2b1d14,#3a2a1c 45%,#1d7a5a 70%,#c9a33d)}
.hero-jars{left:684px;top:222px;width:240px;height:262px;border-radius:14px}
.hero-title{left:79px;top:196px;font-family:"Bangers",sans-serif;font-size:66px;line-height:70px;color:var(--gold-dark);letter-spacing:1px}
.hero-text{left:79px;top:356px;width:480px;font-size:14.5px;line-height:26px;color:var(--text)}
.dots{left:77px;top:473px;display:flex;gap:9px}
.dots span{width:12px;height:12px;border-radius:50%;border:1px solid #333}
.dots .on{background:#111}
.btn{position:absolute;display:flex;align-items:center;justify-content:center;font-family:"Montserrat",sans-serif;font-weight:500;font-size:15px;letter-spacing:.3px}
.btn::after{content:"";position:absolute;left:-5px;top:5px;right:5px;bottom:-5px;border:1px solid currentColor;opacity:.8}
.btn-dark{background:var(--ink);color:var(--white)}
.btn-dark::after{border-color:var(--ink)}
.btn-gold{background:linear-gradient(180deg,var(--gold-light),var(--gold));color:var(--white)}
.btn-gold::after{border-color:var(--gold)}
.btn-light{background:var(--white);color:var(--ink)}
.btn-light::after{border-color:var(--white)}
.about-bg{left:599px;top:625px;width:601px;height:459px;background:var(--cream)}
.about-jar{left:110px;top:690px;width:300px;height:320px;border-radius:30px;transform:rotate(38deg)}
h2{position:absolute;font-family:"Playfair Display",serif;font-weight:700;font-size:37px;color:var(--ink);letter-spacing:.3px}
.about-text{left:656px;top:746px;width:430px;font-size:14px;line-height:26px}
.products-text{left:79px;top:1205px;width:700px;font-size:14.5px;line-height:26px}
.card{position:absolute;top:1302px;width:239px;height:395px;background:var(--cream);border:1px solid #efdfae;text-align:center}
.card .thumb{margin:14px 14px 0;height:207px;background:var(--white);display:flex;align-items:center;justify-content:center}
.card .thumb div{width:88px;height:156px;border-radius:8px}
.card h3{margin-top:34px;font-family:"Montserrat",sans-serif;font-weight:600;font-size:17px;letter-spacing:.5px;color:#222}
.card .price{margin-top:10px;font-family:"Montserrat",sans-serif;font-weight:600;font-size:20px;color:var(--gold)}
.card .buy{display:inline-flex;margin-top:14px;width:105px;height:40px;align-items:center;justify-content:center;background:var(--gold);color:var(--white);font-family:"Montserrat",sans-serif;font-weight:500;font-size:13px}
.news-band{left:0;top:1761px;width:1200px;height:343px;background:linear-gradient(90deg,#b89530,#d6b44c 45%,#cda43a)}
.news-jars{left:77px;top:1824px;width:410px;height:291px;border-radius:16px}
.news-text{left:656px;top:1880px;width:470px;font-size:14px;line-height:26px;color:var(--white)}
.why-text{left:79px;top:2233px;width:470px;font-size:14px;line-height:26px;color:var(--muted)}
.video-block{left:893px;top:2354px;width:229px;height:151px;background:var(--gold-dark)}
.video{left:622px;top:2176px;width:438px;height:292px;background:linear-gradient(135deg,#b9b0a0,#5b4a38 45%,#8a8175 70%,#e8e4dc)}
.play{left:799px;top:2281px;width:84px;height:84px;border-radius:50%;background:var(--white);display:flex;align-items:center;justify-content:center}
.feedback-bg{left:0;top:2571px;width:1200px;height:460px;background:var(--cream)}
.quote-mark{left:540px;top:2660px;font-family:"Playfair Display",serif;font-size:230px;line-height:1;color:#f1e4b8}
.feedback-text{left:255px;top:2726px;width:690px;text-align:center;font-size:14px;line-height:26px;color:var(--text)}
.avatar{left:552px;top:2828px;width:94px;height:94px;border-radius:50%;border:2px solid var(--gold);background:var(--white);padding:5px}
.avatar div{width:100%;height:100%;border-radius:50%;background:linear-gradient(180deg,#e6eef6,#9fbad6)}
.client{left:0;width:1200px;top:2942px;text-align:center;font-family:"Montserrat",sans-serif;font-size:15px;color:var(--gold)}
.footer{left:0;top:3031px;width:1200px;height:179px;background:var(--footer)}
.footer-base{left:0;top:3210px;width:1200px;height:82px;background:var(--footer-base);border-top:1px solid #333;text-align:center;font-size:12px;line-height:82px;color:#888}
.footer-links{left:390px;top:3109px;font-family:"Lato",sans-serif;font-size:16px;color:var(--white);word-spacing:2px}
.social{top:3099px;width:41px;height:41px;background:var(--gold)}
</style>
</head>
<body>
<!-- Hero -->
<div class="abs hero-bg"></div>
<div class="abs brand" style="left:78px;top:60px"><span class="dot"></span>TOLVENMARSK</div>
<nav class="abs nav"><span class="active">HOME</span><span>MGO MANUKA HONEY</span><span>ABOUT US</span><span>CONTACT US</span></nav>
<div class="abs cart"><svg width="24" height="22" viewBox="0 0 24 22"><path d="M1 2h4l3 11h12l3-8H7" fill="none" stroke="#fff" stroke-width="2.2" stroke-linejoin="round"/><circle cx="9" cy="18" r="2" fill="#fff"/><circle cx="19" cy="18" r="2" fill="#fff"/></svg></div>
<div class="abs call">
  <svg width="50" height="50" viewBox="0 0 50 50"><circle cx="25" cy="25" r="21" fill="none" stroke="#111" stroke-width="3.5"/><path d="M17 15c2-2 4 0 5 2s0 3-1 4c1 3 4 6 7 7 1-1 2-2 4-1s4 3 2 5c-2 3-6 3-11-1s-9-10-6-16z" fill="#111"/></svg>
  <div><small>CALL US NOW</small><strong>+64 21 555 0142</strong></div>
</div>
<div class="abs hero-circle"></div>
<div class="abs hero-jars jar-photo" role="img" aria-label="Product photo: two jars of manuka honey"></div>
<div class="abs hero-title">SOMETHING EXCITING IS<br>HAPPENING!</div>
<p class="abs hero-text">Lorem ipsum dolor sit amet, consectetur adipiscing elit, sed deiusmod tempor incididunt ut labore et dolore magna aliqua. Ut enim aminim veniam, quis nostrud exercitation ullamco.</p>
<div class="abs dots"><span></span><span class="on"></span><span></span><span></span></div>
<div class="btn btn-dark" style="left:207px;top:454px;width:146px;height:51px">LEARN MORE</div>
<svg class="abs" style="left:353px;top:430px" width="260" height="52"><path d="M0 50H186V2H258" fill="none" stroke="#b89a50" stroke-width="1"/></svg>

<!-- About -->
<div class="abs about-bg"></div>
<div class="abs about-jar jar-photo" role="img" aria-label="Product photo: tilted jar of manuka honey"></div>
<svg class="abs" style="left:378px;top:875px" width="280" height="117"><path d="M0 1H132V114H277" fill="none" stroke="#333" stroke-width="1"/></svg>
<h2 style="left:656px;top:682px">ABOUT COMPANY</h2>
<p class="abs about-text">Lorem ipsum dolor sit amet, consectetur adipiscing elit, sed do eiusmod tempor incididunt ut labore et dolore magna aliqua. Ut enim ad minim veniam, quis nostrud exercitation ullamco laboris nisi ut aliquip ex ea commodo consequat. Duis aute irure dolor in reprehenderit in voluptate velit esse cillum dolore eu fugiat nulla pariatur. Excepteur sint occaecat cupidatat non proident, sunt in culpa qui officia deserunt mollit anim id est laborum.</p>
<div class="btn btn-gold" style="left:659px;top:958px;width:146px;height:52px">LEARN MORE</div>

<!-- Products -->
<h2 style="left:79px;top:1140px">OUR PRODUCTS</h2>
<p class="abs products-text">Lorem ipsum dolor sit amet, consectetur adipiscing elit, sed deiusmod tempor incididunt ut labore et dolore magna aliqua. Ut enim aminim veniam, quis nostrud exercitation ullamco.</p>
<div class="btn btn-dark" style="left:914px;top:1157px;width:208px;height:51px">VIEW ALL PRODUCTS</div>
<div class="card" style="left:78px"><div class="thumb"><div class="jar-photo" role="img" aria-label="Product photo: jar of manuka honey"></div></div><h3>PRODUCT 1</h3><div class="price">$00.00</div><span class="buy">BUY NOW</span></div>
<div class="card" style="left:346px"><div class="thumb"><div class="jar-photo" role="img" aria-label="Product photo: jar of manuka honey"></div></div><h3>PRODUCT 1</h3><div class="price">$00.00</div><span class="buy">BUY NOW</span></div>
<div class="card" style="left:615px"><div class="thumb"><div class="jar-photo" role="img" aria-label="Product photo: jar of manuka honey"></div></div><h3>PRODUCT 1</h3><div class="price">$00.00</div><span class="buy">BUY NOW</span></div>
<div class="card" style="left:883px"><div class="thumb"><div class="jar-photo" role="img" aria-label="Product photo: jar of manuka honey"></div></div><h3>PRODUCT 1</h3><div class="price">$00.00</div><span class="buy">BUY NOW</span></div>

<!-- Newsletter -->
<div class="abs news-band" role="img" aria-label="Golden-toned photo of a beekeeper among manuka shrubs"></div>
<div class="abs news-jars jar-photo" role="img" aria-label="Product photo: row of honey jars"></div>
<h2 style="left:656px;top:1816px;color:#fff">SIGN UP NEWSLETTER</h2>
<p class="abs news-text">Lorem ipsum dolor sit amet, consectetur adipiscing elit, sed do eiusmod tempor incididunt ut labore et dolore magna aliqua. Ut enim ad minim velit esse cillum dolore eu fugiat nulla pariatur.</p>
<div class="btn btn-light" style="left:659px;top:1990px;width:187px;height:52px">JOIN NEWSLETTER</div>

<!-- Why -->
<h2 style="left:79px;top:2172px">WHY TOLVENMARSK...?</h2>
<p class="abs why-text">Lorem ipsum dolor sit amet, consectetur adipiscing elit, sed do eiusmod tempor incididunt ut labore et dolore magna aliqua. Ut enim ad minim veniam, quis nostrud exercitation ullamco laboris nisi ut aliquip ex ea commodo consequat. Duis aute irure dolor in reprehenderit in voluptate velit esse cillum dolore eu fugiat nulla pariatur. Excepteur sint occaecat cupidatat non proident, sunt in culpa qui officia deserunt mollit anim id est laborum.</p>
<div class="btn btn-gold" style="left:83px;top:2447px;width:146px;height:51px">WATCH VIDEO</div>
<div class="abs video-block"></div>
<div class="abs video" role="img" aria-label="Video still: tea, crepes and a jar of honey on a table"></div>
<div class="abs play"><svg width="24" height="30" viewBox="0 0 24 30"><path d="M3 2l19 13L3 28z" fill="#d4a52a"/></svg></div>

<!-- Feedback -->
<div class="abs feedback-bg"></div>
<h2 style="left:0;width:1200px;text-align:center;top:2630px">CLIENT'S FEEDBACK</h2>
<div class="abs quote-mark">&ldquo;</div>
<p class="abs feedback-text">Lorem ipsum dolor sit amet, consectetur adipiscing elit, sed do eiusmod tempor incididunt ut labore et dolore magna aliqua. Ut enim ad minim veniam, quis nostrud exercitation ullamco laboris nisi ut aliquip ex ea commodo consequat.</p>
<svg class="abs" style="left:256px;top:2866px" width="48" height="18"><path d="M46 9H3M11 2L3 9l8 7" fill="none" stroke="#c8980e" stroke-width="1.6"/></svg>
<svg class="abs" style="left:896px;top:2866px" width="48" height="18"><path d="M2 9h43M37 2l8 7-8 7" fill="none" stroke="#333" stroke-width="1.6"/></svg>
<div class="abs avatar"><div role="img" aria-label="Client portrait photo"></div></div>
<div class="abs client">– &nbsp;Client Name</div>

<!-- Footer -->
<footer>
<div class="abs footer"></div>
<div class="abs brand" style="left:78px;top:3108px"><span class="dot"></span>TOLVENMARSK</div>
<div class="abs footer-links">Home &nbsp;| &nbsp;Mgo Manuka Honey &nbsp;| &nbsp;About Us &nbsp;| &nbsp;Contact Us</div>
<div class="abs social" style="left:978px" role="img" aria-label="Social link"></div>
<div class="abs social" style="left:1030px" role="img" aria-label="Social link"></div>
<div class="abs social" style="left:1081px" role="img" aria-label="Social link"></div>
<div class="abs footer-base">Copyright © TOLVENMARSK - 2020 . All Right Reserved.</div>
</footer>
</body>
</html>
```